Call Center In Need of Website Design

We are a call center that provides inbound and outbound calling & marketing services for eCommerce store. We would like to see a fun, creative, playful design that is simple.

Here are some sample design sites we like;
- https://www.velmoreline.com/
- https://pindrask.io/
- https://www.glimbertic.com/live-chat-software/
- https://www.zavrolin.com/

Here are some competitor sites;
- https://www.ostrevaglinks.com/
- https://www.helpkestrel.com/

I have attached website content for your use.

Target Market(s)

eCommerce

Coding

Coded - Design and coding required

Number of Pages Required

5+ page

Font styles to use
Sans Serif

Colors

Designer to choose colors to be used in the design.

Requirements
Must have
• Must have designs for the following 5 separate pages;
• 1. Home (landing)
• - This will be were the design style really needs to show.
• - Just needs to touch on key services
• - CTA
• 2. About Us
• - Basic page for about me paragraph
• 3. Services
• - List of services with icons
• - Click on service type to expand details or hover over service icon to view popup bubble with details about that service
• 4. Pricing
• - Option to bundle 1(one) digital service plan and 1(one) call center service plan
• - Bundling adds 10% monthly discount to over all price
• - Customer does NOT have to bundle
• - FAQ
• 5. Contact Us
• - Include a capture form (name, company name, email, phone, message)
• - Contact info
• - Business hours
• When customer purchases their desired plan, then they are taken to a page where they must schedule a call with an account rep.
Nice to have
• home page animations
Should not have
• All information on Home/Landing page.

```html
<!DOCTYPE html>
<html lang="en">
<head>
<meta charset="utf-8">
<title>Orbitelle – Omnichannel Customer Care</title>
<link rel="stylesheet" href="https://fonts.googleapis.com/css2?family=Montserrat:wght@500;600;700&family=Questrial&display=swap">
<style>
:root{
  --stage:#eceef2;
  --hero-a:#1f3db5;
  --hero-b:#4c8fc0;
  --hero-c:#73cbb4;
  --indigo:#363b88;
  --indigo-card:#2f3479;
  --teal:#4fbd9c;
  --teal-band:#66c4aa;
  --ink:#2b2b33;
  --muted:#6b6e78;
  --rule:#e2e4e8;
  --night:#1c1c1e;
  --white:#ffffff;
  --head:"Montserrat",sans-serif;
  --body:"Questrial",sans-serif;
}
*{box-sizing:border-box;margin:0;padding:0}
html,body{width:1200px;height:2236px;overflow:hidden}
body{background:var(--stage);font-family:var(--body);color:var(--ink);position:relative}

/* ---------- desktop page ---------- */
.desktop{position:absolute;left:55px;top:40px;width:776px;background:var(--white);box-shadow:0 6px 24px rgba(0,0,0,.12)}
.hero{position:relative;height:359px;overflow:hidden;background:linear-gradient(120deg,var(--hero-a) 0%,var(--hero-b) 45%,var(--hero-c) 100%);color:var(--white)}
.hero .bubble{position:absolute;border-radius:50%;background:rgba(255,255,255,.09)}
.nav{position:absolute;left:104px;right:104px;top:30px;display:flex;align-items:center;justify-content:space-between}
.brand{display:flex;align-items:center;gap:10px;font-family:var(--body);font-size:24px;letter-spacing:4px;color:var(--white)}
.brand .dot{width:26px;height:26px;border-radius:50%;border:2px solid var(--hero-c)}
.nav ul{list-style:none;display:flex;gap:26px;font-family:var(--head);font-size:7px;font-weight:600;letter-spacing:.5px;text-transform:uppercase}
.nav li{opacity:.8}
.nav li.active{opacity:1}
.hero-copy{position:absolute;left:0;right:0;top:145px;text-align:center}
.hero-copy h1{font-family:var(--head);font-weight:600;font-size:28px;line-height:1.15}
.hero-copy p{font-family:var(--body);font-size:27px;line-height:1.2}
.cta{display:flex;justify-content:center;gap:14px;margin-top:30px}
.btn{border:1px solid var(--white);padding:7px 14px;font-family:var(--head);font-size:7px;font-weight:600;color:var(--white)}

.what{height:148px;background:var(--indigo);color:var(--white);display:flex;padding:40px 104px 0;gap:60px;border-bottom:1px solid rgba(255,255,255,.08)}
.what .lead{width:240px}
.what h2{font-family:var(--head);font-weight:600;font-size:17px}
.wordmark{font-family:var(--body);font-size:25px;letter-spacing:5px;margin-top:22px}
.what p{font-size:7.5px;line-height:1.75;opacity:.75;flex:1}

.services{position:relative;height:183px;background:var(--indigo);display:flex;justify-content:center;gap:21px;padding-top:15px}
.card{width:211px;background:var(--indigo-card);color:var(--white);padding:15px 22px}
.card h3{display:flex;align-items:center;gap:9px;font-family:var(--head);font-size:11.5px;font-weight:600}
.card ul{list-style:none;margin:12px 0 0 4px;font-size:7.5px;line-height:1.45;opacity:.85}
.card li::before{content:"";display:inline-block;width:4px;height:4px;border:1px solid #fff;border-radius:50%;margin-right:12px}
.card .more{display:block;margin-top:16px;font-family:var(--head);font-size:6.5px;font-weight:600}

.content{position:relative;height:359px;background:var(--white)}
.content .swoop{position:absolute;left:0;top:0}
.faq{position:absolute;left:104px;right:104px;top:58px;display:flex;gap:110px}
.faq h2{font-family:var(--head);font-size:16px;font-weight:600;color:var(--teal)}
.faq .wordmark{color:var(--ink);margin-top:22px}
.faq .q{width:310px;font-size:7.5px;line-height:1.75;color:var(--muted)}
.faq .q strong{display:block;color:var(--ink);font-family:var(--head);font-size:7px}
.rule{position:absolute;left:104px;right:104px;top:160px;border-top:1px solid var(--rule)}
.about{position:absolute;left:104px;right:104px;top:185px;display:flex;gap:48px}
.art{width:198px;height:134px;border-radius:50% 46% 48% 52%;background:radial-gradient(circle at 55% 50%,#ef6a6a 0 28%,#6fcbb2 29% 100%)}
.about .txt{flex:1;font-size:7.5px;line-height:1.75;color:var(--muted);padding-top:18px}
.about .txt p+p{margin-top:10px}

.foot{height:40px;background:var(--teal-band);color:var(--white);display:flex;align-items:center;padding:0 104px;font-size:7.5px;gap:22px}
.foot .ico{display:flex;align-items:center;gap:6px}
.foot nav{margin-left:auto;display:flex;gap:16px;font-family:var(--head);font-weight:600;font-size:7px}
.copy{height:33px;background:var(--night);color:#cfcfd2;display:flex;align-items:center;justify-content:center;font-size:7px}

/* ---------- mobile page ---------- */
.mobile{position:absolute;left:887px;top:124px;width:264px;background:var(--white);box-shadow:0 6px 24px rgba(0,0,0,.12)}
.m-hero{position:relative;height:364px;overflow:hidden;background:linear-gradient(140deg,var(--hero-a) 0%,var(--hero-b) 50%,var(--hero-c) 100%);color:var(--white);text-align:center}
.m-hero .bubble{position:absolute;border-radius:50%;background:rgba(255,255,255,.09)}
.m-hero .brand{position:absolute;left:14px;top:18px;font-size:23px}
.burger{position:absolute;right:14px;top:74px;width:16px}
.burger span{display:block;height:1.5px;background:#fff;margin-bottom:3.5px}
.m-hero h1{position:absolute;left:0;right:0;top:118px;font-family:var(--head);font-weight:600;font-size:27px;line-height:1.3}
.m-hero h1 span{display:block;font-family:var(--body);font-weight:400}
.m-hero .cta{position:absolute;left:0;right:0;top:277px;margin:0;gap:10px}
.m-hero .btn{font-size:6.5px;padding:7px 12px}

.m-indigo{height:723px;background:var(--indigo);color:var(--white);padding:60px 12px 0}
.m-indigo h2{font-family:var(--head);font-weight:600;font-size:17px}
.m-indigo .wordmark{font-size:24px;margin-top:22px}
.m-indigo p{font-size:7px;line-height:1.95;opacity:.75;margin-top:14px}
.m-card{margin:30px 12px 0;background:var(--indigo-card);padding:14px 16px 20px}
.m-card h3{display:flex;align-items:center;gap:9px;font-family:var(--head);font-size:11.5px;font-weight:600}
.m-card ul{list-style:none;margin:12px 0 0 4px;font-size:7px;line-height:1.55;opacity:.85}
.m-card li::before{content:"";display:inline-block;width:4px;height:4px;border:1px solid #fff;border-radius:50%;margin-right:12px}
.m-card .more{display:block;margin-top:16px;font-family:var(--head);font-size:6px;font-weight:600}

.m-white{height:648px;background:var(--white);padding:44px 12px 0}
.m-white h2{font-family:var(--head);font-size:16px;font-weight:600;color:var(--teal)}
.m-white .wordmark{margin-top:20px;font-size:24px}
.m-white .q{font-size:7px;line-height:1.95;color:var(--muted);margin-top:12px}
.m-white .q strong{display:block;color:var(--ink);font-family:var(--head);font-size:6.5px}
.m-white hr{border:0;border-top:1px solid var(--rule);margin:22px 0 28px}
.m-white .art{width:212px;height:136px;margin:0 auto}
.m-white .txt{font-size:7px;line-height:1.95;color:var(--muted);margin-top:28px}
.m-white .txt p+p{margin-top:12px}

.m-foot{height:188px;background:var(--teal-band);color:var(--white);padding:16px 14px;font-size:7px}
.m-foot .row{display:flex;justify-content:space-between}
.m-foot .ico{display:flex;align-items:center;gap:6px}
.m-foot .phone{margin-top:14px}
.m-foot nav{margin-top:16px;font-family:var(--head);font-weight:600;font-size:6.5px;line-height:1.9;display:flex;flex-direction:column}
.m-copy{height:36px;background:var(--night);color:#cfcfd2;display:flex;align-items:center;justify-content:center;font-size:6.5px}
</style>
</head>
<body>

<main class="desktop">
  <header class="hero">
    <span class="bubble" style="left:150px;top:80px;width:260px;height:260px"></span>
    <span class="bubble" style="left:300px;top:-40px;width:200px;height:200px"></span>
    <span class="bubble" style="left:560px;top:30px;width:250px;height:250px"></span>
    <span class="bubble" style="left:90px;top:270px;width:130px;height:130px"></span>
    <span class="bubble" style="left:260px;top:280px;width:120px;height:120px"></span>
    <nav class="nav">
      <div class="brand"><span class="dot"></span>ORBITELLE</div>
      <ul>
        <li class="active">Home</li><li>About Us</li><li>Services</li><li>Pricing</li><li>Contact Us</li><li>Account</li>
      </ul>
    </nav>
    <div class="hero-copy">
      <h1>Orbitelle Is An Omnichannel</h1>
      <p>Provider For Customer Care</p>
      <div class="cta"><span class="btn">Learn More</span><span class="btn">Plans &amp; Pricing</span></div>
    </div>
  </header>

  <section class="what">
    <div class="lead">
      <h2>What Orbitelle Do</h2>
      <div class="wordmark">ORBITELLE</div>
    </div>
    <p>Orbitelle is your personal customer service and product research team. We love eCommerce, but we love seeing business owners succeed even more! That is exactly why we have developed the processes and technology to take care of the most over looked areas in eCommerce - Customer Service and Retention.<br>Let Orbitelle handle your customers while you focus on growing your business.</p>
  </section>

  <section class="services">
    <article class="card">
      <h3>
        <svg width="22" height="22" viewBox="0 0 22 22" fill="none" stroke="#fff" stroke-width="1.4"><rect x="2" y="3" width="16" height="11" rx="1"/><path d="M1 17h20"/><circle cx="15" cy="14" r="4" fill="var(--indigo-card)"/><path d="M15 12v2l1.5 1"/></svg>
        Digital Services
      </h3>
      <ul><li>Email Support</li><li>Live Chat Support</li><li>Product Research</li><li>Product Listing</li><li>Price Monitoring</li><li>Product Photo &amp; Video Editing</li></ul>
      <span class="more">Learn More</span>
    </article>
    <article class="card">
      <h3>
        <svg width="22" height="22" viewBox="0 0 22 22" fill="none" stroke="#fff" stroke-width="1.4"><circle cx="11" cy="8" r="5"/><path d="M4 20c1-4 4-6 7-6s6 2 7 6"/><path d="M5 8a6 6 0 0 1 12 0"/></svg>
        Call Center Services
      </h3>
      <ul><li>Answering service</li><li>Welcome Calls</li><li>Follow-Up Service</li><li>Customer Upselling</li><li>Over-The-Phone Order Taking</li><li>Order Return Processing</li></ul>
      <span class="more">Learn More</span>
    </article>
  </section>

  <section class="content">
    <svg class="swoop" width="776" height="70" viewBox="0 0 776 70"><path d="M0 0H180C110 4 40 28 0 62Z" fill="var(--indigo)"/></svg>
    <div class="faq">
      <div>
        <h2>Frequently Asked Quetions</h2>
        <div class="wordmark">ORBITELLE</div>
      </div>
      <div class="q">
        <strong>Is the free trial really free?</strong>
        The free trial only relates to the "call center" service packages! There is no hidden fine print or fees to get started. We don't even require any payment info, signatures, or deposits. If you don't like us or our service, just simply walk away.
      </div>
    </div>
    <div class="rule"></div>
    <div class="about">
      <div class="art" role="img" aria-label="Illustration of a laptop, tablet and phone showing chat bubbles on a teal blob"></div>
      <div class="txt">
        <p>Orbitelle is an omnichannel provider for customer care and back-end office support. We primarily work with eCommerce companies around the world. Our service is vital to the core operations and functionality of consumer-focused online eCommerce companies.</p>
        <p>Orbitelle originally started out as a generalized call center support company. Based in California, the founder quickly realized that there was a lack of support for eCommerce owners that were just getting started. In 2018, Orbitelle switched gears to offer professional grade call center support at a price that even start-ups could afford.</p>
      </div>
    </div>
  </section>

  <footer class="foot">
    <span class="ico"><svg width="8" height="10" viewBox="0 0 8 10"><path d="M4 0a4 4 0 0 0-4 4c0 3 4 6 4 6s4-3 4-6a4 4 0 0 0-4-4z" fill="#fff"/></svg>418 Larkmoor Ave Fresno, CA 93720</span>
    <span class="ico"><svg width="10" height="7" viewBox="0 0 10 7"><rect width="10" height="7" fill="#fff"/><path d="M0 0l5 4 5-4" stroke="var(--teal-band)" fill="none"/></svg>info@orbitelle.inc</span>
    <span class="ico"><svg width="8" height="8" viewBox="0 0 8 8"><path d="M1 0l2 2-1 1.5c.7 1.2 1.3 1.8 2.5 2.5L6 5l2 2-1 1C3 8 0 5 0 1z" fill="#fff"/></svg>(800) 555-0147</span>
    <nav><span>Home</span><span>About</span><span>Services</span><span>Pricing</span><span>Contact Us</span><span>Account</span></nav>
  </footer>
  <div class="copy">Copyright © 2018 Orbitelle. All Rights Reserved.</div>
</main>

<main class="mobile">
  <header class="m-hero">
    <span class="bubble" style="left:-40px;top:250px;width:140px;height:140px"></span>
    <span class="bubble" style="left:110px;top:300px;width:120px;height:120px"></span>
    <span class="bubble" style="left:150px;top:60px;width:160px;height:160px"></span>
    <div class="brand"><span class="dot"></span>ORBITELLE</div>
    <div class="burger"><span></span><span></span><span></span></div>
    <h1>Orbitelle Is An<br>Omnichannel<span>Provider For<br>Customer Care</span></h1>
    <div class="cta"><span class="btn">Learn More</span><span class="btn">Plans &amp; Pricing</span></div>
  </header>

  <section class="m-indigo">
    <h2>What Orbitelle Do</h2>
    <div class="wordmark">ORBITELLE</div>
    <p>Orbitelle is your personal customer service and product research team. We love eCommerce, but we love seeing business owners succeed even more! That is exactly why we have developed the processes and technology to take care of the most over looked areas in eCommerce - Customer Service and Retention.<br>Let Orbitelle handle your customers while you focus on growing your business.</p>
    <article class="m-card">
      <h3><svg width="20" height="20" viewBox="0 0 22 22" fill="none" stroke="#fff" stroke-width="1.4"><rect x="2" y="3" width="16" height="11" rx="1"/><path d="M1 17h20"/></svg>Digital Services</h3>
      <ul><li>Email Support</li><li>Live Chat Support</li><li>Product Research</li><li>Product Listing</li><li>Price Monitoring</li><li>Product Photo &amp; Video Editing</li></ul>
      <span class="more">Learn More</span>
    </article>
    <article class="m-card">
      <h3><svg width="20" height="20" viewBox="0 0 22 22" fill="none" stroke="#fff" stroke-width="1.4"><circle cx="11" cy="8" r="5"/><path d="M4 20c1-4 4-6 7-6s6 2 7 6"/></svg>Call Center Services</h3>
      <ul><li>Answering service</li><li>Welcome Calls</li><li>Follow-Up Service</li><li>Customer Upselling</li><li>Over-The-Phone Order Taking</li><li>Order Return Processing</li></ul>
      <span class="more">Learn More</span>
    </article>
  </section>

  <section class="m-white">
    <h2>Frequently Asked Quetions</h2>
    <div class="wordmark">ORBITELLE</div>
    <div class="q"><strong>Is the free trial really free?</strong>The free trial only relates to the "call center" service packages! There is no hidden fine print or fees to get started. We don't even require any payment info, signatures, or deposits. If you don't like us or our service, just simply walk away.</div>
    <hr>
    <div class="art" role="img" aria-label="Illustration of a laptop, tablet and phone showing chat bubbles on a teal blob"></div>
    <div class="txt">
      <p>Orbitelle is an omnichannel provider for customer care and back-end office support. We primarily work with eCommerce companies around the world. Our service is vital to the core operations and functionality of consumer-focused online eCommerce companies.</p>
      <p>Orbitelle originally started out as a generalized call center support company. Based in California, the founder quickly realized that there was a lack of support for eCommerce owners that were just getting started. In 2018, Orbitelle switched gears to offer professional grade call center support at a price that even start-ups could afford.</p>
    </div>
  </section>

  <footer class="m-foot">
    <div class="row">
      <span class="ico"><svg width="7" height="9" viewBox="0 0 8 10"><path d="M4 0a4 4 0 0 0-4 4c0 3 4 6 4 6s4-3 4-6a4 4 0 0 0-4-4z" fill="#fff"/></svg>418 Larkmoor Ave Fresno, CA 93720</span>
      <span class="ico"><svg width="9" height="6" viewBox="0 0 10 7"><rect width="10" height="7" fill="#fff"/></svg>info@orbitelle.inc</span>
    </div>
    <div class="ico phone"><svg width="7" height="7" viewBox="0 0 8 8"><path d="M1 0l2 2-1 1.5c.7 1.2 1.3 1.8 2.5 2.5L6 5l2 2-1 1C3 8 0 5 0 1z" fill="#fff"/></svg>(800) 555-0147</div>
    <nav><span>Home</span><span>About Us</span><span>Services</span><span>Pricing</span><span>Contact Us</span><span>Account</span></nav>
  </footer>
  <div class="m-copy">Copyright © 2018 Orbitelle. All Rights Reserved.</div>
</main>

</body>
</html>
```